Logo, Web and Mobile Designs for enterprise social media platform

All the details are in the attached document, please start reading the scope document first which explains what is this project about and the details about the needed deliverables, after that please read the UI_Requirements document which will detail what is expected regarding the coded web version since this is a coded contest, it is very important that you meet the UI requirements or suggest something else but we will need to agree first before working on the coded version

Good Luck

Target Market(s)

Enterprise Social Media

Industry/Entity Type

Media

Coding

Coded - Design and coding required

Number of Pages Required

5+ page

Font styles to use
Sans Serif

Requirements
Must have
• All the must haves are listed in the scope document so please check before you start

```html
<!DOCTYPE html>
<html lang="en">
<head>
<meta charset="utf-8">
<title>Teamora – Enterprise Social Network</title>
<link href="https://fonts.googleapis.com/css2?family=Hind:wght@400;500;600&family=Open+Sans:ital,wght@0,400;0,600;1,400&display=swap" rel="stylesheet">
<style>
:root{
  --blue:#1a73c8;
  --topbar:#474747;
  --footer:#3b3b3b;
  --page:#f2f2f2;
  --card:#ffffff;
  --ink:#2b2b2b;
  --text:#555555;
  --line:#dddddd;
  --footer-text:#bbbbbb;
  --play-bg:rgba(40,44,50,.55);
}
*{box-sizing:border-box;margin:0;padding:0}
html,body{width:1200px;height:2242px;overflow:hidden}
body{background:var(--page);font-family:"Open Sans",sans-serif;color:var(--text);font-size:12px;line-height:1.7;position:relative}
a{color:inherit;text-decoration:none}
.heading{font-family:"Hind",sans-serif;color:var(--ink);font-weight:500}

.topbar{height:39px;background:var(--topbar);display:flex;align-items:center;justify-content:space-between;padding:0 100px;color:#e0e0e0;font-size:12px}
.topbar-icons{display:flex;gap:16px;align-items:center}
.topbar-links{display:flex;gap:34px}
.topbar-links .caret{margin-left:8px;font-size:9px}

.header{height:79px;background:#fff;display:flex;align-items:center;justify-content:space-between;padding:0 100px;box-shadow:0 1px 3px rgba(0,0,0,.08);position:relative;z-index:2}
.brand{font-family:"Hind",sans-serif;font-weight:600;font-size:31px;color:var(--blue);letter-spacing:.2px}
.main-nav{display:flex;gap:38px;font-size:12px;color:#444}
.main-nav .active{color:var(--blue)}
.main-nav .caret{margin-left:10px;font-size:9px}

.hero{position:relative;height:433px;background:linear-gradient(90deg,#c9ccce 0%,#dfe2e3 30%,#cfd2d3 55%,#8d8f92 78%,#5a5c60 100%)}
.hero-copy{position:absolute;left:100px;top:86px;width:520px}
.hero-title{font-size:31px;line-height:44px;color:#333}
.hero-text{margin-top:8px;font-size:12px;line-height:20px;color:#333;width:460px}
.btn{display:inline-block;background:var(--blue);color:#fff;font-family:"Hind",sans-serif;font-weight:600;font-size:14px;border-radius:3px;box-shadow:0 2px 3px rgba(0,0,0,.2)}
.hero .btn{margin-top:24px;width:97px;height:39px;line-height:41px;text-align:center}
.dots{display:flex;gap:9px;margin-top:28px;padding-left:2px}
.dots span{width:6px;height:6px;border-radius:50%;background:#eee}
.dots .on{background:var(--blue)}

.content{display:flex;gap:21px;padding:47px 100px 0}
.posts{width:673px;display:flex;flex-direction:column;gap:33px}
.sidebar{width:307px;display:flex;flex-direction:column;gap:22px}
.card{background:var(--card);box-shadow:0 1px 4px rgba(0,0,0,.14);border-radius:2px}

.post{padding:15px 16px 0}
.post-media{height:245px;position:relative}
.media-city{background:linear-gradient(180deg,#e4e6e8 0%,#bfc2c5 45%,#7f8388 100%)}
.media-crowd{background:linear-gradient(90deg,#dfe5ea 0%,#c4ccd4 40%,#e8ecef 70%,#b9c2ca 100%)}
.media-team{background:linear-gradient(90deg,#e9ebec 0%,#cfd4d8 45%,#8c97a3 75%,#3c4653 100%)}
.play{position:absolute;left:50%;top:50%;width:52px;height:52px;margin:-26px 0 0 -26px;background:var(--play-bg);border:2px solid #fff;border-radius:50%;display:flex;align-items:center;justify-content:center}
.post-title{font-size:20px;line-height:25px;margin-top:22px;max-width:590px}
.post-date{font-size:11.5px;margin-top:6px;color:#555}
.post-text{margin-top:4px;line-height:20px;width:590px}
.post-stats{display:flex;gap:18px;margin:16px 0 36px;font-size:12.5px;color:#444;align-items:center}
.post-stats span{display:flex;align-items:center;gap:6px}

.widget{padding:20px 20px 24px}
.widget-title{font-size:20px;line-height:26px;margin-bottom:14px}
.category-list{list-style:none;font-size:11.5px;line-height:20.6px;color:#555;padding-left:3px}
.event-list{margin-top:12px}
.event{display:flex;gap:10px;margin-bottom:31px}
.event:last-child{margin-bottom:0}
.event-thumb{width:80px;height:72px;flex:none;margin-left:3px}
.thumb-a{background:linear-gradient(135deg,#6d6a66,#2a2a2a)}
.thumb-b{background:linear-gradient(135deg,#a6774f,#d9c3a9)}
.thumb-c{background:linear-gradient(135deg,#e7e7e7,#8b8f95)}
.thumb-d{background:linear-gradient(135deg,#2d3a45,#c9c09a)}
.event-text{font-size:11.5px;line-height:20.5px;color:#555;padding-top:2px}
.event-date{font-style:italic;color:var(--blue)}
.tweet-list{margin-top:18px}
.tweet{display:flex;gap:14px;margin-bottom:30px}
.tweet:last-child{margin-bottom:0}
.tweet-dot{width:9px;height:9px;border-radius:50%;background:var(--blue);flex:none;margin-top:6px;margin-left:3px}
.tweet-body{width:228px;font-size:11.5px;line-height:20.6px;color:#555}
.tweet-body .link{color:var(--blue)}
.tweet-actions{display:flex;gap:10px;margin-top:8px;color:var(--blue)}
.newsletter-text{font-size:11.5px;line-height:20.5px;color:#555}
.field{margin-top:16px;height:45px;border:1px solid var(--line);padding:0 14px;line-height:43px;font-size:11.5px;color:#999}
.newsletter .btn{margin-top:26px;width:89px;height:35px;line-height:37px;text-align:center;font-family:"Open Sans",sans-serif;font-weight:400;font-size:13px;border-radius:2px}

.footer{position:absolute;left:0;top:2143px;width:1200px;height:99px;background:var(--footer);padding:26px 100px 0;color:var(--footer-text);font-size:12px}
.footer-nav{display:flex;gap:40px}
.copyright{margin-top:6px;font-size:11.5px}
.social{position:absolute;right:106px;top:32px;display:flex;gap:16px}
.social span{width:11px;height:11px;border-radius:50%;background:#c8c8c8}
</style>
</head>
<body>
<div class="topbar">
  <div class="topbar-icons">
    <svg width="11" height="11" viewBox="0 0 12 12" fill="#dcdcdc"><circle cx="6" cy="3.5" r="3"/><path d="M0 12c0-4 3-5.5 6-5.5s6 1.5 6 5.5z"/></svg>
    <svg width="13" height="11" viewBox="0 0 14 12" fill="#dcdcdc"><ellipse cx="6" cy="5" rx="6" ry="4.2"/><path d="M2 8l-1 3 4-2z"/></svg>
    <svg width="11" height="11" viewBox="0 0 12 12"><circle cx="6" cy="6" r="5" fill="none" stroke="#dcdcdc" stroke-width="2"/><path d="M1 6h10M6 1v10" stroke="#dcdcdc"/></svg>
  </div>
  <nav class="topbar-links"><a>Home</a><a>Profile</a><a>Account<span class="caret">&#8964;</span></a></nav>
</div>

<header class="header">
  <div class="brand">Teamora</div>
  <nav class="main-nav">
    <a class="active">Home</a><a>Events</a><a>Business Opportunities<span class="caret">&#8964;</span></a><a>Feature Article<span class="caret">&#8964;</span></a><a>Support</a><a>Contact</a>
  </nav>
</header>

<section class="hero" role="img" aria-label="Smiling businessman in a suit and glasses in a bright, blurred office">
  <div class="hero-copy">
    <h1 class="heading hero-title">The World Moves Fast.<br>Move Faster With Teamora</h1>
    <p class="hero-text">Neque porro quisquam est, qui dolorem ipsum quia dolor sit amet, consectetur, adipisci velit, sed quia non numquam</p>
    <a class="btn">Read More</a>
    <div class="dots"><span class="on"></span><span></span><span></span></div>
  </div>
</section>

<main class="content">
  <div class="posts">
    <article class="card post">
      <div class="post-media media-city" role="img" aria-label="Businessman looking out over a city skyline from a rooftop"></div>
      <h2 class="heading post-title">Social media refer to internet based applications such as, for instance, social networks, blogs</h2>
      <div class="post-date">Nov18,2015</div>
      <p class="post-text">Nemo enim ipsam voluptatem quia voluptas sit aspernatur aut odit aut fugit, sed quia consequuntur magni dolores eos qui ratione voluptatem sequi nesciunt.</p>
      <div class="post-stats">
        <span><svg width="15" height="12" viewBox="0 0 15 12" fill="#444"><ellipse cx="6" cy="4.5" rx="6" ry="4"/><path d="M2 7l-1 3 4-2zM9 9.5c3 0 6-1 6-3.5 0-1-1-2-2-2.5z"/></svg>5</span>
        <span><svg width="13" height="12" viewBox="0 0 13 12" fill="#444"><rect x="0" y="5" width="3" height="7"/><path d="M4 5l3-5c1.5 0 2 1 1.5 3H12c1 0 1.3 1 1 2l-1.5 6H4z"/></svg>15</span>
        <span><svg width="14" height="12" viewBox="0 0 14 12" fill="#444"><path d="M8 0l6 5-6 5V7C4 7 1.5 8.5 0 12c0-5 3-8.5 8-8.5z"/></svg>15</span>
      </div>
    </article>

    <article class="card post">
      <div class="post-media media-crowd" role="img" aria-label="Video still: motion-blurred crowd of commuters walking through a bright hall">
        <span class="play"><svg width="14" height="16" viewBox="0 0 14 16" fill="#fff"><path d="M1 0l13 8-13 8z"/></svg></span>
      </div>
      <h2 class="heading post-title">Social media refer to internet based applications such as, for instance, social networks, blogs</h2>
      <div class="post-date">Nov18,2015</div>
      <p class="post-text">Nemo enim ipsam voluptatem quia voluptas sit aspernatur aut odit aut fugit, sed quia consequuntur magni dolores eos qui ratione voluptatem sequi nesciunt.</p>
      <div class="post-stats">
        <span><svg width="15" height="12" viewBox="0 0 15 12" fill="#444"><ellipse cx="6" cy="4.5" rx="6" ry="4"/><path d="M2 7l-1 3 4-2zM9 9.5c3 0 6-1 6-3.5 0-1-1-2-2-2.5z"/></svg>5</span>
        <span><svg width="13" height="12" viewBox="0 0 13 12" fill="#444"><rect x="0" y="5" width="3" height="7"/><path d="M4 5l3-5c1.5 0 2 1 1.5 3H12c1 0 1.3 1 1 2l-1.5 6H4z"/></svg>15</span>
        <span><svg width="14" height="12" viewBox="0 0 14 12" fill="#444"><path d="M8 0l6 5-6 5V7C4 7 1.5 8.5 0 12c0-5 3-8.5 8-8.5z"/></svg>15</span>
      </div>
    </article>

    <article class="card post">
      <div class="post-media media-team" role="img" aria-label="Three colleagues smiling while looking at a laptop together"></div>
      <h2 class="heading post-title">Social media refer to internet based applications such as, for instance, social networks, blogs</h2>
      <div class="post-date">Nov18,2015</div>
      <p class="post-text">Nemo enim ipsam voluptatem quia voluptas sit aspernatur aut odit aut fugit, sed quia consequuntur magni dolores eos qui ratione voluptatem sequi nesciunt.</p>
      <div class="post-stats">
        <span><svg width="15" height="12" viewBox="0 0 15 12" fill="#444"><ellipse cx="6" cy="4.5" rx="6" ry="4"/><path d="M2 7l-1 3 4-2zM9 9.5c3 0 6-1 6-3.5 0-1-1-2-2-2.5z"/></svg>5</span>
        <span><svg width="13" height="12" viewBox="0 0 13 12" fill="#444"><rect x="0" y="5" width="3" height="7"/><path d="M4 5l3-5c1.5 0 2 1 1.5 3H12c1 0 1.3 1 1 2l-1.5 6H4z"/></svg>15</span>
        <span><svg width="14" height="12" viewBox="0 0 14 12" fill="#444"><path d="M8 0l6 5-6 5V7C4 7 1.5 8.5 0 12c0-5 3-8.5 8-8.5z"/></svg>15</span>
      </div>
    </article>
  </div>

  <aside class="sidebar">
    <section class="card widget">
      <h3 class="heading widget-title">Categories</h3>
      <ul class="category-list">
        <li>Overview</li><li>Financial Services</li><li>Healthcare</li><li>Life Sciences</li><li>Communications</li><li>Retail</li><li>Media</li><li>Government</li><li>Manufacturing</li><li>Automotive</li><li>Higher Ed</li><li>Nonprofit</li>
      </ul>
    </section>

    <section class="card widget">
      <h3 class="heading widget-title">Recent Events</h3>
      <div class="event-list">
        <div class="event"><div class="event-thumb thumb-a" role="img" aria-label="Man reading a tablet"></div><div class="event-text">The enterprise social network that connects<div class="event-date">Nov18,2015</div></div></div>
        <div class="event"><div class="event-thumb thumb-b" role="img" aria-label="Coffee cup on a wooden table"></div><div class="event-text">The enterprise social network that connects<div class="event-date">Nov18,2015</div></div></div>
        <div class="event"><div class="event-thumb thumb-c" role="img" aria-label="Person working at a laptop"></div><div class="event-text">The enterprise social network that connects<div class="event-date">Nov18,2015</div></div></div>
        <div class="event"><div class="event-thumb thumb-d" role="img" aria-label="Man beneath a glowing light bulb"></div><div class="event-text">The enterprise social network that connects<div class="event-date">Nov18,2015</div></div></div>
      </div>
    </section>

    <section class="card widget">
      <h3 class="heading widget-title">Recent Tweets</h3>
      <div class="tweet-list">
        <div class="tweet"><span class="tweet-dot"></span><div class="tweet-body">Neque porro quisquam est, qui dolorem ipsum quia dolor sit amet, consectetur, adipisci velit, <span class="link">sed quia non numquam eius modi tempora</span> incidunt ut labore et dolore magnam aliquam quaerat voluptatem.
          <div class="tweet-actions"><svg width="12" height="10" viewBox="0 0 12 10" fill="none" stroke="#1a73c8" stroke-width="1.6"><path d="M2 8V2h6M10 2v6H4"/></svg><svg width="12" height="10" viewBox="0 0 14 12" fill="#1a73c8"><path d="M8 0l6 5-6 5V7C4 7 1.5 8.5 0 12c0-5 3-8.5 8-8.5z"/></svg><svg width="12" height="10" viewBox="0 0 12 10" fill="#1a73c8"><path d="M6 10L1 5C-1 2 2-1 6 2c4-3 7 0 5 3z"/></svg></div></div></div>
        <div class="tweet"><span class="tweet-dot"></span><div class="tweet-body">Neque porro quisquam est, qui dolorem ipsum quia dolor <span class="link">sit amet, consectetur,</span> adipisci velit,
          <div class="tweet-actions"><svg width="12" height="10" viewBox="0 0 12 10" fill="none" stroke="#1a73c8" stroke-width="1.6"><path d="M2 8V2h6M10 2v6H4"/></svg><svg width="12" height="10" viewBox="0 0 14 12" fill="#1a73c8"><path d="M8 0l6 5-6 5V7C4 7 1.5 8.5 0 12c0-5 3-8.5 8-8.5z"/></svg><svg width="12" height="10" viewBox="0 0 12 10" fill="#1a73c8"><path d="M6 10L1 5C-1 2 2-1 6 2c4-3 7 0 5 3z"/></svg></div></div></div>
      </div>
    </section>

    <section class="card widget newsletter">
      <h3 class="heading widget-title">Subscribe Newsletter</h3>
      <p class="newsletter-text">Subscribe newsletter to receive the latest news and updates direct to your inbox.</p>
      <div class="field">Enter Your MailId</div>
      <a class="btn">Submit</a>
    </section>
  </aside>
</main>

<footer class="footer">
  <nav class="footer-nav"><a>Home</a><a>Events</a><a>Business Opportunities</a><a>Feature Article</a><a>Support</a><a>Contact</a></nav>
  <p class="copyright">© Copyright 2015 Teamora. All rights reserved.</p>
  <div class="social"><span></span><span></span><span></span><span></span><span></span></div>
</footer>
</body>
</html>
```